WP website design for Kemble

We need a wordpress design that will incorporate a professional color scheme with company logo in a clean layout. The design needs to consider that this will be developed on a responsive theme. Colors are will be the green of the logo and any others that will creatively highlight it.

Industry/Entity Type

It Company

Font styles to use
Sans Serif

Requirements
Must have
• Navigation: 1) Home 2) Auctions 3) Auction Services 4) Sellers 5) TR Kemble Livestock 6) About Us 7) Contact Us
Site will have slideshow element, image attached.
Widgets will be: 1)Email Signup form 2) Featured Auctions widget 3) Social Media (FB, Youtube, RSS) 4) News & Events blog
Footer will have smaller company logo, association logos (attached) and contact info (below)
▪ T.R. Kemble Inc. / Auctioneers
▪ 4710 NC Hwy 91
▪ Linwood, NC 27612
▪ Office: (555) 318-6402
▪ Cell: (555) 274-8813
▪ email: trkemble@trkemble-example.com
Nice to have
• Site will have drop-down menus - please indicate the styling, for instance the dropdown menus

```html
<!DOCTYPE html>
<html lang="en">
<head>
<meta charset="utf-8">
<title>T.R. Kemble Inc. / Auctioneers</title>
<link href="https://fonts.googleapis.com/css2?family=Source+Sans+3:wght@400;600;700&family=Arimo:wght@400;700&display=swap" rel="stylesheet">
<style>
:root{
  --bg-green:#215f0e;
  --brand-green:#2f7d14;
  --header-green:#368a18;
  --deep-green:#1d5a0c;
  --yellow:#dfcb0b;
  --yellow-light:#e9d84a;
  --panel:#ebebeb;
  --panel-border:#b9b9b9;
  --text:#222;
  --link:#2f6a9a;
  --btn:#333;
}
*{margin:0;padding:0;box-sizing:border-box}
html,body{width:847px;height:1200px;overflow:hidden}
body{background:var(--bg-green);font-family:"Arimo",Arial,sans-serif;color:var(--text);position:relative}
.page{position:absolute;left:70px;top:27px;width:707px;height:1152px;background:#fff}

.nav{position:absolute;left:0;top:0;width:707px;height:34px;background:var(--yellow);display:flex;font-family:"Source Sans 3",sans-serif;font-weight:600;font-size:11px;letter-spacing:.2px}
.nav a{display:flex;align-items:center;justify-content:center;color:#1a1a1a;text-decoration:none;border-right:1px solid #c6b300;height:100%}
.nav a:last-child{border-right:none}
.dropdown{position:absolute;left:72px;top:34px;width:139px;z-index:5;font-family:"Source Sans 3",sans-serif;font-size:11.5px}
.dropdown div{height:23px;line-height:23px;padding-left:10px}
.dropdown .item{background:var(--yellow-light);color:#2a2a2a}
.dropdown .item.active{background:var(--deep-green);color:#fff;border-bottom:4px solid var(--yellow);height:27px}

.hero{position:absolute;left:0;top:34px;width:707px;height:236px;overflow:hidden}
.brand-panel{position:absolute;left:0;top:0;width:224px;height:236px;background:linear-gradient(#fff,#f0f0f0)}
.slide{position:absolute;left:224px;top:0;width:483px;height:236px;background:linear-gradient(#e9eef2 0%,#c9d4dc 22%,#8a7a5a 45%,#b2702e 62%,#a8712f 70%,#6d6a55 82%,#3f5060 100%)}
.brand{position:absolute;left:18px;top:102px;width:200px;color:var(--brand-green);font-family:"Source Sans 3",sans-serif;font-weight:600;font-size:20px;line-height:26px;text-align:center}
.brand .dot{display:block;width:40px;height:40px;border-radius:50%;background:var(--brand-green);margin:0 auto 8px}
.hero-curve{position:absolute;left:0;top:216px}

.listing{position:absolute;left:18px;width:433px;height:219px;background:#f1f1f1;border:1px solid var(--panel-border)}
.listing h2{height:32px;background:var(--header-green);color:#fff;font-size:12px;font-weight:700;line-height:32px;padding-left:15px;letter-spacing:.1px}
.thumb{position:absolute;left:26px;top:42px;width:112px;height:76px;background:linear-gradient(#cfd8dd 0%,#c5cec8 28%,#7c9159 36%,#6a8a45 70%,#8a9a62 100%);box-shadow:2px 2px 3px rgba(0,0,0,.35)}
.btn{position:absolute;left:52px;width:72px;height:24px;background:var(--btn);color:#eee;border-radius:3px;font-size:9.5px;display:flex;align-items:center;padding-left:8px;gap:6px}
.btn svg{flex:none}
.l-date{position:absolute;left:158px;top:50px;font-size:12.5px;font-weight:700;letter-spacing:.3px}
.l-desc{position:absolute;left:158px;top:73px;width:226px;font-size:9.6px;line-height:13px}
.l-bill{position:absolute;left:233px;top:103px;font-size:10.5px;font-weight:700;color:var(--link)}
.l-info{position:absolute;left:158px;top:126px;font-size:9.6px;line-height:13.7px}
.l-info b{font-weight:700}
.pin{display:inline-block;vertical-align:-2px;margin-right:3px}
.l-when{position:absolute;left:205px;top:195px;font-size:9.6px}

.widget{position:absolute;left:478px;width:217px;background:var(--panel);border:1px solid var(--panel-border);border-radius:3px}
.widget h3{font-family:"Source Sans 3",sans-serif;font-weight:600;font-size:18.5px;color:#222}
.signup{position:absolute;left:478px;top:308px;width:217px;height:106px;background:var(--yellow);border-radius:4px;overflow:hidden}
.signup .at{position:absolute;right:16px;top:-6px;font-family:"Source Sans 3",sans-serif;font-size:72px;font-weight:700;color:#cfb70a}
.signup h3{position:absolute;left:13px;top:6px;font-family:"Source Sans 3",sans-serif;font-weight:600;font-size:18.5px;color:var(--deep-green)}
.signup p{position:absolute;left:13px;top:34px;width:185px;font-size:9.5px;line-height:12.5px;color:#333}
.signup .field{position:absolute;left:13px;top:68px;width:131px;height:25px;background:#fff;font-size:9px;color:#555;line-height:25px;padding-left:7px}
.signup .submit{position:absolute;left:144px;top:68px;width:61px;height:25px;background:var(--deep-green);color:#fff;font-family:"Source Sans 3",sans-serif;font-weight:700;font-size:12.5px;text-align:center;line-height:25px}
.featured{top:435px;height:245px;text-align:center}
.featured h3{margin:16px 0 0 15px;text-align:left}
.featured .f-title{margin-top:12px;font-size:8.6px;font-weight:700;line-height:14px}
.featured .f-photo{width:126px;height:77px;margin:9px auto 0;border:2px solid var(--brand-green);background:linear-gradient(#d7e2ea 0%,#b5c6a4 35%,#8d9b85 55%,#6f8a58 75%,#5b7d43 100%)}
.featured .f-loc{margin-top:18px;font-size:8.8px;line-height:12px}
.news{top:706px;height:170px}
.news h3{margin:9px 0 0 13px}
.news ul{list-style:none;margin:5px 0 0 15px;font-size:8.6px;line-height:11px;width:172px}
.news li{margin-bottom:9px}
.social{top:903px;height:100px}
.social h3{margin:7px 0 0 13px}
.social .icons{position:absolute;left:14px;top:47px;display:flex;gap:19px}
.social .icon{width:36px;height:36px;border-radius:50%;border:3px solid #c9c9c9}
.social .icon.one{background:#3f5f9a}
.social .icon.two{background:#c8302a}
.social .icon.three{background:#e8832a}

.footer{position:absolute;left:0;top:1038px;width:707px;height:114px;background:var(--yellow)}
.f-contact{position:absolute;left:19px;top:16px;font-size:9.6px;line-height:14.3px;color:#111}
.f-brand{position:absolute;left:346px;top:26px;width:90px;text-align:center;color:var(--brand-green);font-family:"Source Sans 3",sans-serif;font-weight:600;font-size:11px;line-height:13px}
.f-brand .dot{display:block;width:16px;height:16px;border-radius:50%;background:var(--brand-green);margin:0 auto 4px}
.badge{position:absolute;background:#2b2b2b}
.copyright{position:absolute;left:0;top:96px;width:707px;text-align:center;font-size:8.7px;color:#111}
</style>
</head>
<body>
<div class="page">

  <nav class="nav">
    <a style="width:66px">HOME</a>
    <a style="width:91px">AUCTIONS</a>
    <a style="width:131px">AUCTION SERVICES</a>
    <a style="width:80px">SELLERS</a>
    <a style="width:151px">TR KEMBLE LIVESTOCK</a>
    <a style="width:87px">ABOUT US</a>
    <a style="width:101px">CONTACT US</a>
  </nav>

  <div class="dropdown">
    <div class="item">Upcoming Auction</div>
    <div class="item active">Past Auction</div>
  </div>

  <header class="hero">
    <div class="brand-panel"></div>
    <div class="brand"><span class="dot"></span>T.R. Kemble Inc.<br>/ Auctioneers</div>
    <div class="slide" role="img" aria-label="Slideshow photo: bare autumn trees on dry orange grass beside a still pond"></div>
    <svg class="hero-curve" width="707" height="20" viewBox="0 0 707 20">
      <path d="M0 3 Q300 24 707 5 L707 20 L0 20 Z" fill="#fff"/>
      <path d="M0 3 Q300 24 707 5" fill="none" stroke="#dfcb0b" stroke-width="2"/>
    </svg>
  </header>

  <article class="listing" style="top:307px">
    <h2>ONLINE ONLY RIDLEY AUCTION - REAL ESTATE</h2>
    <div class="thumb" role="img" aria-label="Open grassland under a pale sky"></div>
    <div class="btn" style="top:131px"><svg width="12" height="11"><rect x="1" y="1" width="10" height="7" rx="2" fill="#cfe3f2"/><path d="M3 8 L3 11 L6 8Z" fill="#cfe3f2"/></svg>Details</div>
    <div class="btn" style="top:163px"><svg width="12" height="11"><rect x="1" y="1" width="10" height="9" fill="#7bbf5a"/><rect x="1" y="1" width="10" height="3" fill="#e4a33a"/></svg>Photos</div>
    <div class="l-date">THURSDAY, AUGUST 21ST AT 10:00 A.M.</div>
    <div class="l-desc">Selling 3120 Acres of land in tracts of 2590 Acres &amp; 560 Acres</div>
    <div class="l-bill">Click here to view Sale Bill!</div>
    <div class="l-info">LIVE OFF-SITE AUCTION<br><b>Auction Location:</b><br><svg class="pin" width="8" height="11"><path d="M4 11 L0.6 5 A3.6 3.6 0 1 1 7.4 5Z" fill="#d11"/></svg>118 N Main St, Fairview, OK 73760<br><b>Property Location:</b><br><svg class="pin" width="8" height="11"><path d="M4 11 L0.6 5 A3.6 3.6 0 1 1 7.4 5Z" fill="#d11"/></svg>118 N Main St, Fairview, OK 73760</div>
    <div class="l-when">08/21/14 at 10:00 AM CDT</div>
  </article>

  <article class="listing" style="top:556px">
    <h2>ONLINE ONLY RIDLEY AUCTION - REAL ESTATE</h2>
    <div class="thumb" role="img" aria-label="Open grassland under a pale sky"></div>
    <div class="btn" style="top:131px"><svg width="12" height="11"><rect x="1" y="1" width="10" height="7" rx="2" fill="#cfe3f2"/><path d="M3 8 L3 11 L6 8Z" fill="#cfe3f2"/></svg>Details</div>
    <div class="btn" style="top:163px"><svg width="12" height="11"><rect x="1" y="1" width="10" height="9" fill="#7bbf5a"/><rect x="1" y="1" width="10" height="3" fill="#e4a33a"/></svg>Photos</div>
    <div class="l-date">THURSDAY, AUGUST 21ST AT 10:00 A.M.</div>
    <div class="l-desc">Selling 3120 Acres of land in tracts of 2590 Acres &amp; 560 Acres</div>
    <div class="l-bill">Click here to view Sale Bill!</div>
    <div class="l-info">LIVE OFF-SITE AUCTION<br><b>Auction Location:</b><br><svg class="pin" width="8" height="11"><path d="M4 11 L0.6 5 A3.6 3.6 0 1 1 7.4 5Z" fill="#d11"/></svg>118 N Main St, Fairview, OK 73760<br><b>Property Location:</b><br><svg class="pin" width="8" height="11"><path d="M4 11 L0.6 5 A3.6 3.6 0 1 1 7.4 5Z" fill="#d11"/></svg>118 N Main St, Fairview, OK 73760</div>
    <div class="l-when">08/21/14 at 10:00 AM CDT</div>
  </article>

  <article class="listing" style="top:799px">
    <h2>ONLINE ONLY RIDLEY AUCTION - REAL ESTATE</h2>
    <div class="thumb" role="img" aria-label="Open grassland under a pale sky"></div>
    <div class="btn" style="top:131px"><svg width="12" height="11"><rect x="1" y="1" width="10" height="7" rx="2" fill="#cfe3f2"/><path d="M3 8 L3 11 L6 8Z" fill="#cfe3f2"/></svg>Details</div>
    <div class="btn" style="top:163px"><svg width="12" height="11"><rect x="1" y="1" width="10" height="9" fill="#7bbf5a"/><rect x="1" y="1" width="10" height="3" fill="#e4a33a"/></svg>Photos</div>
    <div class="l-date">THURSDAY, AUGUST 21ST AT 10:00 A.M.</div>
    <div class="l-desc">Selling 3120 Acres of land in tracts of 2590 Acres &amp; 560 Acres</div>
    <div class="l-bill">Click here to view Sale Bill!</div>
    <div class="l-info">LIVE OFF-SITE AUCTION<br><b>Auction Location:</b><br><svg class="pin" width="8" height="11"><path d="M4 11 L0.6 5 A3.6 3.6 0 1 1 7.4 5Z" fill="#d11"/></svg>118 N Main St, Fairview, OK 73760<br><b>Property Location:</b><br><svg class="pin" width="8" height="11"><path d="M4 11 L0.6 5 A3.6 3.6 0 1 1 7.4 5Z" fill="#d11"/></svg>118 N Main St, Fairview, OK 73760</div>
    <div class="l-when">08/21/14 at 10:00 AM CDT</div>
  </article>

  <aside>
    <section class="signup">
      <span class="at">@</span>
      <h3>Email Signup</h3>
      <p>Please join our free mailing list to get auction alerts.</p>
      <div class="field">Enter Your Email</div>
      <div class="submit">Submit</div>
    </section>

    <section class="widget featured">
      <h3>Featured Auctions</h3>
      <div class="f-title">13.35 ACRES OF PRIME DEVELOP<br>&amp; 33RD STREET</div>
      <div class="f-photo" role="img" aria-label="White farmhouse with a crowd gathered on the lawn"></div>
      <div class="f-loc">LOTS 13 &amp; 14 FOR SALE, MILLBROOK<br>IOWA<br>Elm Street, Millbrook, IA 52640</div>
    </section>

    <section class="widget news">
      <h3>News Events</h3>
      <ul>
        <li>Great Land Auction Companies Make All the Difference</li>
        <li>Great OK Farms for Sale at Auction Prices</li>
        <li>Farmland Auctions on Route 66</li>
        <li>Great Land Auction Companies Make All the Difference</li>
        <li>Great OK Farms for Sale at Auction Prices</li>
      </ul>
    </section>

    <section class="widget social">
      <h3>Social Media</h3>
      <div class="icons">
        <span class="icon one" role="img" aria-label="Social profile link"></span>
        <span class="icon two" role="img" aria-label="Video channel link"></span>
        <span class="icon three" role="img" aria-label="News feed link"></span>
      </div>
    </section>
  </aside>

  <footer class="footer">
    <div class="f-contact">T.R. Kemble Inc. / Auctioneers<br>4710 NC Hwy 91<br>Linwood, NC 27612<br>Office: (555) 318-6402 , Cell: (555) 274-8813<br>Email: trkemble@trkemble-example.com</div>
    <div class="f-brand"><span class="dot"></span>T.R. Kemble Inc.<br>/ Auctioneers</div>
    <div class="badge" style="left:456px;top:32px;width:82px;height:30px;border-radius:4px"></div>
    <div class="badge" style="left:552px;top:27px;width:60px;height:40px;border-radius:6px"></div>
    <div class="badge" style="left:626px;top:20px;width:58px;height:58px;border-radius:50%"></div>
    <div class="copyright">Copyright © 2014 T.R. Kemble, Inc. / Auctioneers. All Rights Reserved.</div>
  </footer>
</div>
</body>
</html>
```